Business Card (double-sided) and Stationary Design for dental office

1) Business Card Design: We need a business card design for a dental specialty office.
Texts should contain:
The name of our office "Brindle Oaks Orthodontics"
Tagline: "Specialist in Orthodontic and Maxillofacial Orthopedics"
Tag line: "Creating "Tolvering" smiles for Children and Adults"
Doctor name: "Doctor Name"
Office Address:
"123 Street Name
City, State Zip code"
Office email address: office@brindleoaksortho.com
Website: www.brindleoaksortho.com

We will provide the full office address once the design is selected
Theme: beach, paradise, coastal, wave
We would like to have some creativity in design. Some acceptable ideas: front page: logo and office name. Back page: more detail information, and map to office in form of an island. Please see sample from our other location, but you DON'T HAVE TO USE OR COPY THE SAME CONCEPT.

IF POSSIBLE, PLEASE SUBMIT AT LEAST TWO CONCEPTS: ONE WITH THE BACK LOOKING SIMILAR TO WHAT IS IN THE SAMPLE, AND ONE DIFFERENT.

Color: designer to choose. We have different shade of blues and sand color in our office. Please see logo.

2) Please also design a matching set of stationary that compliment the business card and our logo.

Target Market(s)

Dental

Contact Information for Business Card

See descriptions

Font styles to use
Other font styles liked:
• Matching texts in logo

Colors
0054AA
0677BA
7BADD7
CADEEF
E8F1F8
0094D4
00A9DD
6FCCEA
C7EBF8
E9F6FB
00AB8E
00BBA5
67D7C9
C6EFE9
E9F9F6

Requirements
Must have
• Double-sided
Nice to have
• Beach coastal theme
Should not have
• Any shape or drawing of of tooth or teeth. We don’t need these. You don't necessarily have to just cut and paste the logo art and text as a whole, you have the liberty to rearrange the text.

```html
<!DOCTYPE html>
<html lang="en">
<head>
<meta charset="utf-8">
<title>Brindle Oaks Orthodontics – Appointment Card &amp; Business Card</title>
<link rel="stylesheet" href="https://fonts.googleapis.com/css2?family=Montserrat:wght@500;600;700&family=Open+Sans:wght@400;600&display=swap">
<style>
  :root {
    --teal-deep: #3a8fa8;
    --teal-mint: #7ecdbf;
    --ink: #4a4a4a;
    --ink-soft: #5c5c5c;
    --paper: #ffffff;
    --backdrop: #ecefef;
    --line: #7a7a7a;
  }
  * { box-sizing: border-box; margin: 0; padding: 0; }
  html, body { width: 1200px; height: 900px; overflow: hidden; }
  body {
    background: var(--backdrop);
    font-family: "Open Sans", Arial, sans-serif;
    color: var(--ink);
    position: relative;
  }
  .card {
    position: absolute;
    width: 560px;
    height: 320px;
    background: var(--paper);
    box-shadow: 0 6px 18px rgba(0,0,0,.18);
    overflow: hidden;
  }

  /* Appointment card */
  .appointment-card { left: 60px; top: 100px; display: flex; flex-direction: column; }
  .appointment-card__header {
    background: var(--teal-deep);
    color: var(--paper);
    height: 58px;
    display: flex; align-items: center; justify-content: center;
    font-family: "Montserrat", Arial, sans-serif;
    font-weight: 600; font-size: 24px; letter-spacing: .3px;
  }
  .appointment-card__body { flex: 1; padding: 22px 34px 0 40px; font-family: "Montserrat", Arial, sans-serif; font-size: 16px; color: var(--ink-soft); }
  .field-row { display: flex; align-items: baseline; gap: 8px; margin-bottom: 16px; }
  .field { display: flex; align-items: baseline; gap: 6px; }
  .field--grow { flex: 1; }
  .field__line { flex: 1; border-bottom: 2px dotted var(--line); height: 1px; min-width: 40px; }
  .field--date { width: 230px; }
  .field--time { flex: 1; margin-left: 12px; }
  .weekdays { display: flex; gap: 14px; font-size: 14px; margin-bottom: 12px; }
  .weekday { display: flex; align-items: center; gap: 5px; }
  .weekday__box { width: 20px; height: 15px; border: 1.5px solid var(--ink-soft); }
  .notice { font-size: 14px; color: var(--ink-soft); }
  .appointment-card__footer {
    background: var(--teal-mint);
    height: 50px;
    display: flex; align-items: center; justify-content: center;
    color: var(--paper);
    font-family: "Montserrat", Arial, sans-serif;
    font-weight: 600; font-size: 15px;
  }

  /* Business card */
  .business-card { left: 580px; top: 480px; }
  .business-card__wave { position: absolute; inset: 0; width: 560px; height: 320px; }
  .person { position: absolute; left: 34px; top: 48px; }
  .person__name { font-family: "Montserrat", Arial, sans-serif; font-weight: 700; font-size: 24px; color: var(--teal-deep); }
  .person__title { font-size: 14px; color: var(--ink); margin-top: 0; }
  .brand { position: absolute; right: 28px; top: 34px; display: flex; flex-direction: column; align-items: center; gap: 8px; }
  .brand__dot { width: 58px; height: 58px; border-radius: 50%; background: var(--teal-deep); }
  .brand__name { font-family: "Montserrat", Arial, sans-serif; font-weight: 600; font-size: 18px; color: var(--teal-deep); }
  .contact { position: absolute; left: 48px; top: 150px; font-size: 14px; color: var(--ink); line-height: 1.35; }
  .contact__address { margin-bottom: 14px; }
  .contact__item { display: flex; align-items: center; gap: 7px; }
  .contact__icon { width: 14px; height: 14px; flex: none; }
  .business-card__tagline {
    position: absolute; right: 26px; bottom: 26px;
    text-align: center; color: var(--paper);
    font-family: "Montserrat", Arial, sans-serif; font-weight: 500; font-size: 14px; line-height: 1.3;
  }
</style>
</head>
<body>

<section class="card appointment-card" aria-label="Appointment card">
  <header class="appointment-card__header">Your Next Appointment on</header>
  <div class="appointment-card__body">
    <div class="field-row">
      <div class="field field--grow"><span>Name:</span><span class="field__line"></span></div>
    </div>
    <div class="field-row">
      <div class="field field--date"><span>Date :</span><span class="field__line"></span></div>
      <div class="field field--time"><span>Time :</span><span class="field__line"></span><span>AM / PM</span></div>
    </div>
    <div class="weekdays">
      <span class="weekday"><span class="weekday__box"></span>MON</span>
      <span class="weekday"><span class="weekday__box"></span>TUE</span>
      <span class="weekday"><span class="weekday__box"></span>WED</span>
      <span class="weekday"><span class="weekday__box"></span>THU</span>
      <span class="weekday"><span class="weekday__box"></span>FRI</span>
      <span class="weekday"><span class="weekday__box"></span>SAT</span>
    </div>
    <p class="notice">If unable to keep appointment, kindly give 24hrs notice.</p>
  </div>
  <footer class="appointment-card__footer">Creating Tolvering smiles for Children and Adults</footer>
</section>

<section class="card business-card" aria-label="Business card">
  <svg class="business-card__wave" viewBox="0 0 560 320" aria-hidden="true">
    <path d="M0 262 C140 275 260 250 360 190 C430 150 490 110 560 84 L560 110 C490 132 430 170 360 212 C260 270 140 290 0 282 Z" fill="var(--teal-mint)"/>
    <path d="M0 290 C150 300 270 275 370 214 C440 172 500 135 560 114 L560 320 L0 320 Z" fill="var(--teal-deep)"/>
  </svg>

  <div class="person">
    <p class="person__name">Marcus Ellery</p>
    <p class="person__title">Managing Director</p>
  </div>

  <div class="brand">
    <span class="brand__dot"></span>
    <span class="brand__name">Brindle Oaks Orthodontics</span>
  </div>

  <div class="contact">
    <p class="contact__address">123 Street Name<br>City, State Zip code</p>
    <p class="contact__item">
      <svg class="contact__icon" viewBox="0 0 14 14" aria-hidden="true"><rect x="1" y="3" width="12" height="8" fill="var(--teal-deep)"/><path d="M1 3 L7 8 L13 3" stroke="#fff" stroke-width="1.2" fill="none"/></svg>
      office@brindleoaksortho.com
    </p>
    <p class="contact__item">
      <svg class="contact__icon" viewBox="0 0 14 14" aria-hidden="true"><circle cx="7" cy="7" r="6" fill="var(--teal-deep)"/><path d="M1 7 H13 M7 1 V13 M3 3.5 Q7 5.5 11 3.5 M3 10.5 Q7 8.5 11 10.5" stroke="#fff" stroke-width=".9" fill="none"/></svg>
      www.brindleoaksortho.com
    </p>
  </div>

  <p class="business-card__tagline">Specialist in Orthodontic and<br>Maxillofacial Orthopedics</p>
</section>

</body>
</html>
```